Velmora Systems Website

Website design for our company: Velmora Systems.
The website should look fresh and IT focused. Please have a look at http://www.velmorasystems.example.au/ for our current design. We want something fresh and new, professional looking, in WordPress so we can easily make changes.

It Company

```html
<!DOCTYPE html>
<html lang="en">
<head>
<meta charset="utf-8">
<title>Velmora Systems</title>
<link href="https://fonts.googleapis.com/css2?family=Open+Sans:wght@300;400&family=Michroma&family=Ubuntu:wght@500&display=swap" rel="stylesheet">
<style>
:root{
  --ink:#3a3f44;
  --teal:#4294a9;
  --teal-light:#cfe6ec;
  --link:#2f8ea6;
  --cyan:#3ab7d6;
  --header:#0b0b0b;
  --footer:#232323;
  --panel:#ececec;
  --tab:#a9a9a9;
  --white:#ffffff;
}
*{margin:0;padding:0;box-sizing:border-box}
html,body{width:1023px;height:1200px;overflow:hidden;background:var(--white)}
body{position:relative;font-family:Arial,Helvetica,sans-serif;color:var(--ink)}
.abs{position:absolute}

/* header */
.site-header{left:0;top:0;width:1023px;height:113px;background:linear-gradient(#3a3a3a 0,#111 45px,#000 70px,#050505 113px)}
.brand{left:119px;top:12px;display:flex;align-items:center;gap:7px}
.brand-mark{width:26px;height:26px;background:var(--teal);flex:none}
.brand-name{font-family:"Open Sans",sans-serif;font-weight:300;font-size:27px;color:var(--white);letter-spacing:.5px;line-height:1;white-space:nowrap}
.tagline{left:121px;top:44px;font-family:"Open Sans",sans-serif;font-size:11px;color:var(--cyan);letter-spacing:-.2px}
.top-links{right:117px;top:43px;font-size:9.5px;color:var(--cyan)}
.top-links span{margin:0 3px;color:#aaa}
.nav{left:113px;top:68px;width:799px;height:39px;border-radius:12px;background:#1e1f21;box-shadow:inset 0 1px 0 #333;display:flex;gap:4px;padding:6px 7px}
.nav a{flex:1;height:25px;border-radius:7px;background:linear-gradient(#3b3d40,#222325);color:#fff;font-family:"Michroma",sans-serif;font-size:9.5px;text-decoration:none;display:flex;align-items:center;justify-content:center;letter-spacing:.6px}
.nav a.active{background:linear-gradient(#fdfdfd,#c6c8cb);color:#222}

/* hero */
.hero{left:0;top:113px;width:1023px;height:341px;background:linear-gradient(100deg,#8fb6cd 0%,#3f6f8a 25%,#1d4052 50%,#17424c 75%,#1b2227 100%)}
.hero-copy{left:348px;top:199px;width:270px;color:#eaf4f8}
.hero-copy h1{font-family:"Open Sans",sans-serif;font-weight:300;font-size:28px;color:#fff;letter-spacing:-.6px;line-height:1.1;white-space:nowrap}
.hero-copy p{font-size:12px;line-height:14.3px;margin-top:2px}

/* features */
.features{left:0;top:454px;width:1023px;height:226px;background:var(--teal)}
.feature{top:24px;width:240px;text-align:center;color:#e4f1f4}
.feature .icon{width:56px;height:56px;border-radius:50%;background:var(--teal-light);margin:0 auto;display:flex;align-items:center;justify-content:center}
.feature h2{font-family:"Open Sans",sans-serif;font-weight:300;font-size:30px;color:#fff;margin-top:14px;line-height:1.1}
.feature p{font-size:12px;line-height:14.5px;margin-top:6px}

/* how it works */
.section-title{font-family:"Open Sans",sans-serif;font-weight:300;font-size:30px;color:var(--ink);letter-spacing:-.3px;line-height:1}
.tabs{left:113px;top:766px;display:flex;gap:1px}
.tabs div{width:81px;height:27px;background:var(--tab);color:#fff;font-size:10.5px;display:flex;align-items:center;justify-content:center}
.tabs div.current{background:var(--panel);color:#222}
.panel{left:113px;top:793px;width:499px;height:191px;background:var(--panel)}
.panel-photo{left:10px;top:12px;width:202px;height:168px;background:#fff;padding:4px}
.panel-photo div{width:100%;height:100%;background:linear-gradient(120deg,#a9c6e0,#5a7fa8 55%,#26374f)}
.panel-text{left:227px;top:37px;width:260px;font-size:12px;line-height:14.5px;color:#333}
.panel-text p+p{margin-top:14px}

.services-list{left:672px;top:768px;list-style:none}
.services-list li{height:25.6px;font-size:12px;color:var(--link);display:flex;align-items:center;gap:7px}
.services-list svg{flex:none}

/* footer */
.site-footer{left:0;top:1035px;width:1023px;height:165px;background:var(--footer)}
.foot-brand{left:119px;top:27px;display:flex;align-items:center;gap:5px}
.foot-brand .brand-mark{width:15px;height:15px}
.foot-brand .brand-name{font-size:14px;letter-spacing:0}
.copyright{left:119px;top:52px;font-size:9px;color:#ddd}
.foot-col{top:26px}
.foot-col h3{font-family:"Ubuntu",sans-serif;font-weight:500;font-size:15px;color:#fff}
.foot-col ul{list-style:none;margin-top:12px}
.foot-col li{font-size:10px;color:var(--link);height:18.8px;display:flex;align-items:center;gap:8px;letter-spacing:.2px}
.foot-col li::before{content:"";border-left:3px solid #ddd;border-top:2.5px solid transparent;border-bottom:2.5px solid transparent}
.email{left:732px;top:1088px;width:158px;height:21px;border-radius:3px;background:#1a1a1a;border:1px solid #3d3d3d;font-size:10px;color:#aaa;padding:4px 12px}
.subscribe{left:825px;top:1119px;width:68px;height:22px;border-radius:4px;background:linear-gradient(#38b2d2,#1f8eac);color:#fff;font-family:"Ubuntu",sans-serif;font-size:10px;display:flex;align-items:center;justify-content:center}
</style>
</head>
<body>

<header class="site-header abs">
  <div class="brand abs"><span class="brand-mark"></span><span class="brand-name">VELMORA SYSTEMS</span></div>
  <div class="tagline abs">IT SERVICES FOR EXPERIENCE ENGINEERS</div>
  <div class="top-links abs">Support<span>|</span>FAQs<span>|</span>Testimonials<span>|</span>Help</div>
  <nav class="nav abs">
    <a class="active">HOME</a><a>CLIENTS</a><a>SERVICES</a><a>SUPPORT</a><a>ABOUT US</a><a>CONTACT US</a>
  </nav>
</header>

<section class="hero abs" role="img" aria-label="Glass office tower and a businessman holding a laptop, with digital data overlays"></section>
<div class="hero-copy abs">
  <h1>LOREM IPSUM DOLOR</h1>
  <p>Duis aute irure dolor in reprehenderit in voluptate velit esse cillum dolore eu fugiat nulla pariatur. Excepteur sint occaecat cupidatat non proident, sunt in culpa qui officia deserunt mollit anim id est laborum.</p>
</div>

<section class="features abs">
  <div class="feature abs" style="left:106px">
    <div class="icon"><svg width="30" height="30" viewBox="0 0 30 30"><g fill="#333a40"><circle cx="14" cy="14" r="8"/><g stroke="#333a40" stroke-width="4"><line x1="14" y1="3" x2="14" y2="25"/><line x1="3" y1="14" x2="25" y2="14"/><line x1="6" y1="6" x2="22" y2="22"/><line x1="22" y1="6" x2="6" y2="22"/></g></g><circle cx="14" cy="14" r="3.5" fill="#cfe6ec"/><line x1="12" y1="12" x2="26" y2="26" stroke="#333a40" stroke-width="4" stroke-linecap="round"/></svg></div>
    <h2>ADVANTAGES</h2>
    <p>Lorem ipsum dolor sit amet, consectetur adipisicing elit, sed do eiusmod tempor incididunt ut labore et dolore magna aliqua.</p>
  </div>
  <div class="feature abs" style="left:380px">
    <div class="icon"><svg width="32" height="32" viewBox="0 0 32 32" fill="none" stroke="#333a40"><circle cx="15" cy="17" r="12" stroke-width="3.5"/><circle cx="15" cy="17" r="5" stroke-width="3"/><line x1="15" y1="17" x2="27" y2="5" stroke-width="2.5"/><path d="M24 3l4 1 1 4" stroke-width="2"/></svg></div>
    <h2>MISSION</h2>
    <p>Sed ut perspiciatis, unde omnis iste natus error sit voluptatem accusantium doloremque laudantium, totam rem aperiam.</p>
  </div>
  <div class="feature abs" style="left:658px">
    <div class="icon"><svg width="32" height="32" viewBox="0 0 32 32" fill="none" stroke="#333a40" stroke-width="2"><path d="M11 19a7 7 0 1 1 10 0v3h-10z"/><line x1="12" y1="25" x2="20" y2="25"/><line x1="13" y1="28" x2="19" y2="28"/><path d="M14 21v-6l2 2 2-2v6"/><g stroke-width="1.8"><line x1="16" y1="1" x2="16" y2="4"/><line x1="5" y1="5" x2="7" y2="7"/><line x1="27" y1="5" x2="25" y2="7"/><line x1="1" y1="14" x2="4" y2="14"/><line x1="28" y1="14" x2="31" y2="14"/></g></svg></div>
    <h2>VISION</h2>
    <p>Lorem ipsum dolor sit amet, consectetur adipisicing elit, sed do eiusmod tempor incididunt ut labore et dolore magna aliqua.</p>
  </div>
</section>

<h2 class="section-title abs" style="left:115px;top:725px">HOW IT WORKS</h2>
<div class="tabs abs"><div class="current">STEP 1</div><div>STEP 2</div><div>STEP 3</div></div>
<div class="panel abs">
  <div class="panel-photo abs"><div role="img" aria-label="Two engineers inspecting a server rack in a data centre"></div></div>
  <div class="panel-text abs">
    <p>At vero eos et accusamus et iusto odio dignissimos ducimus, qui blanditiis praesentium voluptatum deleniti atque corrupti, quos dolores et quas molestias excepturi sint,</p>
    <p>Obcaecati cupiditate non provident, similique sunt in culpa, qui officia deserunt mollitia animi, id est laborum et dolorum fuga.</p>
  </div>
</div>

<h2 class="section-title abs" style="left:669px;top:725px">SERVICES</h2>
<ul class="services-list abs">
  <li><svg width="7" height="9" viewBox="0 0 7 9"><path d="M1 1l4 3.5L1 8" stroke="#666" stroke-width="2" fill="none"/></svg>At vero eos et accusamus et iusto odio</li>
  <li><svg width="7" height="9" viewBox="0 0 7 9"><path d="M1 1l4 3.5L1 8" stroke="#666" stroke-width="2" fill="none"/></svg>Qui blanditiis praesentium voluptatum</li>
  <li><svg width="7" height="9" viewBox="0 0 7 9"><path d="M1 1l4 3.5L1 8" stroke="#666" stroke-width="2" fill="none"/></svg>Nam libero tempore, cum soluta nobis est</li>
  <li><svg width="7" height="9" viewBox="0 0 7 9"><path d="M1 1l4 3.5L1 8" stroke="#666" stroke-width="2" fill="none"/></svg>Temporibus autem quibusdam et aut</li>
  <li><svg width="7" height="9" viewBox="0 0 7 9"><path d="M1 1l4 3.5L1 8" stroke="#666" stroke-width="2" fill="none"/></svg>At vero eos et accusamus et iusto odio</li>
  <li><svg width="7" height="9" viewBox="0 0 7 9"><path d="M1 1l4 3.5L1 8" stroke="#666" stroke-width="2" fill="none"/></svg>Qui blanditiis praesentium voluptatum</li>
  <li><svg width="7" height="9" viewBox="0 0 7 9"><path d="M1 1l4 3.5L1 8" stroke="#666" stroke-width="2" fill="none"/></svg>Nam libero tempore, cum soluta nobis est</li>
  <li><svg width="7" height="9" viewBox="0 0 7 9"><path d="M1 1l4 3.5L1 8" stroke="#666" stroke-width="2" fill="none"/></svg>Temporibus autem quibusdam et aut</li>
  <li><svg width="7" height="9" viewBox="0 0 7 9"><path d="M1 1l4 3.5L1 8" stroke="#666" stroke-width="2" fill="none"/></svg>Nam libero tempore, cum soluta nobis est</li>
</ul>

<footer class="site-footer abs">
  <div class="foot-brand abs"><span class="brand-mark"></span><span class="brand-name">VELMORA SYSTEMS</span></div>
  <div class="copyright abs">© Copyright Software 2014</div>
  <div class="foot-col abs" style="left:289px"><h3>Why Us</h3><ul><li>Our Clients</li><li>Technology</li><li>Soft Labs</li></ul></div>
  <div class="foot-col abs" style="left:391px"><h3>Quick Links</h3><ul><li>Lorem ipsum dolor</li><li>Amet consectetuer</li><li>Mauris vel tortor vitae</li><li>Nibh condimentum</li></ul></div>
  <div class="foot-col abs" style="left:562px"><h3>Support</h3><ul><li>Nibh condimentum</li><li>Integer ac lacus</li><li>Sociis natoque</li><li>Enatibus et magnis</li></ul></div>
  <div class="foot-col abs" style="left:732px"><h3>Newsletter:</h3></div>
</footer>
<div class="email abs">Enter your email here</div>
<div class="subscribe abs">SUBSCRIBE</div>

</body>
</html>
```